Website Design for Architecture Practice

I need a home page and one sidebar/content page for an Architecture practice delivered in PSD.

This archictecture practice specialises in one-off, high end homes and commercial properties (restaurant) heavily influenced by Edmund Harcourt Vale, particularly his work on the Pellworth Museum

I am looking for a home page, and a generic content page where we can outline our services, and showcase our homes.

http://journals.kestrelhill.edu.au/artnotes/Pellworth%20Quayside%202.jpg

Target Market(s)

30-70yr old (typically wealthy) property buyers, developers and investors

Industry/Entity Type

Architecture

Number of Pages Required

2 page

Font styles to use
Serif
Sans Serif

Requirements
Must have
• Home page design
• a Content Page design (ie, top nav with sidebar)
Nice to have
• Use any Edmund Harcourt Vale images you can find via google etc as placeholders for our own photography (ie they don't need to be licensed as we will be replacing with our own commissioned photography). Full color preferred but feel free to experiment with treating any images as you see fit.

```html
<!DOCTYPE html>
<html lang="en">
<head>
<meta charset="utf-8">
<title>Ashcombe Studio</title>
<link rel="stylesheet" href="https://fonts.googleapis.com/css2?family=Marcellus&family=Open+Sans:wght@400;600&display=swap">
<style>
:root{
  --red:#c8202f;
  --ink:#333333;
  --grey:#8a8a8a;
  --footer:#2b2b2b;
  --footer-bar:#1f1f1f;
  --white:#ffffff;
}
*{box-sizing:border-box;margin:0;padding:0}
html,body{width:736px;height:1200px;overflow:hidden;background:var(--white)}
body{font-family:"Open Sans",Arial,sans-serif;color:var(--ink);position:relative}

/* header */
.site-header{position:absolute;top:0;left:0;width:736px;height:74px;background:var(--white)}
.brand{position:absolute;left:98px;top:22px;display:flex;align-items:center;gap:8px}
.brand-mark{width:20px;height:20px;background:var(--red)}
.brand-name{font-family:"Marcellus",Georgia,serif;font-size:19px;color:var(--red);white-space:nowrap}
.phone{position:absolute;right:92px;top:14px;font-size:10px;color:var(--red);display:flex;align-items:center;gap:4px}
.main-nav{position:absolute;right:92px;top:42px;display:flex}
.main-nav a{font-size:9px;letter-spacing:.5px;text-transform:uppercase;color:var(--ink);text-decoration:none;padding:5px 9px}
.main-nav a.active{background:var(--ink);color:var(--white)}

/* hero */
.hero{position:absolute;top:74px;left:0;width:736px;height:323px;
  background:linear-gradient(180deg,#c7cdd0 0%,#a9a9a1 25%,#7a5a44 45%,#5b4031 62%,#3f5a2c 80%,#2d4420 100%)}
.hero-arrow{position:absolute;top:150px;width:14px;height:24px}
.hero-arrow.prev{left:10px}.hero-arrow.next{right:10px}
.hero-caption{position:absolute;left:0;right:0;top:254px;text-align:center;color:var(--white);
  font-family:"Marcellus",Georgia,serif;font-size:15px;line-height:19px;text-shadow:0 1px 3px rgba(0,0,0,.6)}
.hero-dots{position:absolute;left:0;right:0;top:308px;display:flex;justify-content:center;gap:6px}
.hero-dots span{width:6px;height:6px;border-radius:50%;background:rgba(255,255,255,.55)}
.hero-dots span.on{background:var(--white)}

/* welcome */
.welcome{position:absolute;top:397px;left:0;width:736px;height:253px;background:var(--white)}
.welcome-head{position:absolute;left:110px;top:36px;display:flex;align-items:center;gap:10px}
.welcome-head .brand-mark{width:26px;height:26px}
.welcome-title{font-family:"Marcellus",Georgia,serif;font-weight:400;color:var(--red);font-size:17px;line-height:20px}
.welcome-text{position:absolute;left:110px;top:86px;width:282px;font-size:7.5px;line-height:12px;color:var(--grey)}
.btn-more{position:absolute;left:110px;top:170px;background:var(--red);color:var(--white);font-size:7px;padding:4px 9px;border-radius:2px}
.photo{position:absolute;border-radius:50%;border:4px solid var(--white);box-shadow:0 1px 4px rgba(0,0,0,.25)}
.photo.one{left:418px;top:14px;width:150px;height:150px;background:linear-gradient(160deg,#cfd6da,#8d7a68 55%,#5a6b3c)}
.photo.two{left:402px;top:126px;width:96px;height:96px;background:linear-gradient(160deg,#b8b1a5,#6f4b33 60%,#3e5030)}
.photo.three{left:522px;top:98px;width:124px;height:124px;background:linear-gradient(170deg,#9fc2d8,#d9c7a3 50%,#6a7a4a)}

/* services band */
.services{position:absolute;top:650px;left:0;width:736px;height:227px;background:var(--red)}
.service{position:absolute;top:0;width:180px;text-align:center;color:var(--white)}
.service:nth-child(1){left:94px}.service:nth-child(2){left:278px}.service:nth-child(3){left:461px}
.service-icon{margin:32px auto 0;width:72px;height:72px;border-radius:50%;border:2px solid var(--white);display:flex;align-items:center;justify-content:center}
.service-title{font-family:"Marcellus",Georgia,serif;font-weight:400;font-size:14px;margin-top:12px}
.service-text{font-size:7px;line-height:11px;margin:8px auto 0;width:160px;color:#f6d9dc}
.service-dot{width:9px;height:9px;border-radius:50%;background:var(--white);margin:12px auto 0}

/* facilities & gallery */
.lower{position:absolute;top:877px;left:0;width:736px;height:180px;background:var(--white)}
.section-title{font-family:"Marcellus",Georgia,serif;font-weight:400;font-size:15px;color:var(--ink);position:absolute;top:40px}
.facilities-title{left:98px}
.gallery-title{left:277px}
.facility-list{position:absolute;left:98px;top:70px;list-style:none}
.facility-list li{font-size:7px;color:var(--grey);line-height:13px;display:flex;align-items:center;gap:5px}
.facility-list li::before{content:"";width:4px;height:4px;background:var(--red);border-radius:50%}
.gallery{position:absolute;left:277px;top:70px;display:flex;gap:10px}
.gallery-item{width:112px;height:80px}
.gallery-item.a{background:linear-gradient(170deg,#c9d3d8,#7b5a42 55%,#4a5f33)}
.gallery-item.b{background:linear-gradient(170deg,#7f8c6a,#c9c2b1 50%,#3d5228)}
.gallery-item.c{background:linear-gradient(170deg,#8a4f2c,#c88a52 50%,#5a3520)}

/* footer */
.site-footer{position:absolute;top:1057px;left:0;width:736px;height:143px;background:var(--footer);color:#bdbdbd}
.footer-col{position:absolute;top:14px}
.footer-col h4{font-family:"Marcellus",Georgia,serif;font-weight:400;font-size:8px;letter-spacing:.5px;text-transform:uppercase;color:var(--white);margin-bottom:8px}
.footer-col p{font-size:6.5px;line-height:12px}
.footer-col.links{left:110px}
.footer-col.links p::before{content:"› ";color:var(--red)}
.footer-col.contact{left:233px}
.footer-col.map{left:392px}
.map-box{width:120px;height:62px;background:linear-gradient(135deg,#e6e2d6,#cfd8c4 60%,#b9cbd8)}
.footer-col.follow{left:558px}
.social{display:flex;align-items:center;gap:6px;font-size:6.5px;line-height:16px}
.social span{width:10px;height:10px;background:#4a4a4a}
.footer-bar{position:absolute;left:0;bottom:0;width:736px;height:24px;background:var(--footer-bar);font-size:6.5px;color:#8d8d8d;text-align:center;line-height:24px}
</style>
</head>
<body>

<header class="site-header">
  <div class="brand"><span class="brand-mark"></span><span class="brand-name">Ashcombe Studio</span></div>
  <div class="phone">
    <svg width="9" height="9" viewBox="0 0 24 24" aria-hidden="true"><path fill="#c8202f" d="M6.6 10.8a15.1 15.1 0 0 0 6.6 6.6l2.2-2.2c.3-.3.7-.4 1-.2 1.1.4 2.3.6 3.6.6.6 0 1 .4 1 1V20c0 .6-.4 1-1 1A17 17 0 0 1 3 4c0-.6.4-1 1-1h3.5c.6 0 1 .4 1 1 0 1.3.2 2.5.6 3.6.1.3 0 .7-.2 1z"/></svg>
    0400 218 675
  </div>
  <nav class="main-nav">
    <a class="active" href="#">Home</a><a href="#">About</a><a href="#">Services</a><a href="#">Gallery</a><a href="#">Contact</a>
  </nav>
</header>

<section class="hero" role="img" aria-label="Photograph of a long, low timber-and-glass house among trees">
  <svg class="hero-arrow prev" viewBox="0 0 14 24" aria-hidden="true"><path d="M11 2 3 12l8 10" fill="none" stroke="#fff" stroke-width="2.5"/></svg>
  <svg class="hero-arrow next" viewBox="0 0 14 24" aria-hidden="true"><path d="m3 2 8 10-8 10" fill="none" stroke="#fff" stroke-width="2.5"/></svg>
  <p class="hero-caption">We Are An Architecture Business / Practice That Specialises In One-Off<br>High End Homes And Commercial Properties</p>
  <div class="hero-dots"><span class="on"></span><span></span><span></span></div>
</section>

<section class="welcome">
  <div class="welcome-head">
    <span class="brand-mark"></span>
    <h1 class="welcome-title">Welcome to<br>Ashcombe Studio</h1>
  </div>
  <p class="welcome-text">We design one-off homes and commercial spaces rooted in landscape, craft and honest materials. Every project starts with listening to the site and the people who will live there, then builds toward spaces that feel calm, open and timeless.</p>
  <span class="btn-more">Read More</span>
  <div class="photo one" role="img" aria-label="Photograph of a cantilevered house over a waterfall"></div>
  <div class="photo two" role="img" aria-label="Photograph of a brick and timber house exterior"></div>
  <div class="photo three" role="img" aria-label="Photograph of a curved modern building under blue sky"></div>
</section>

<section class="services">
  <div class="service">
    <div class="service-icon"><svg width="38" height="30" viewBox="0 0 38 30" aria-hidden="true"><g fill="none" stroke="#fff" stroke-width="2"><path d="M3 14 19 3l16 11"/><path d="M7 12v16h24V12"/><rect x="15" y="18" width="8" height="10"/></g></svg></div>
    <h2 class="service-title">One Off</h2>
    <p class="service-text">Bespoke residences drawn around the site, light and the way you live.</p>
    <div class="service-dot"></div>
  </div>
  <div class="service">
    <div class="service-icon"><svg width="38" height="30" viewBox="0 0 38 30" aria-hidden="true"><g fill="none" stroke="#fff" stroke-width="2"><path d="M2 12h34"/><path d="M6 12v16h26V12"/><path d="M10 12 19 4l9 8"/><rect x="11" y="17" width="5" height="5"/><rect x="22" y="17" width="5" height="5"/></g></svg></div>
    <h2 class="service-title">High End Homes</h2>
    <p class="service-text">Private houses with crafted detail, fine materials and generous open rooms.</p>
    <div class="service-dot"></div>
  </div>
  <div class="service">
    <div class="service-icon"><svg width="34" height="34" viewBox="0 0 34 34" aria-hidden="true"><g fill="none" stroke="#fff" stroke-width="2"><rect x="6" y="4" width="14" height="28"/><rect x="20" y="14" width="9" height="18"/><path d="M10 9h6M10 14h6M10 19h6M10 24h6M23 19h3M23 24h3"/></g></svg></div>
    <h2 class="service-title">Commercial Properties</h2>
    <p class="service-text">Restaurants and workplaces designed to welcome guests and reflect your brand.</p>
    <div class="service-dot"></div>
  </div>
</section>

<section class="lower">
  <h3 class="section-title facilities-title">Our Facilities</h3>
  <ul class="facility-list">
    <li>Site surveys and feasibility studies</li>
    <li>Concept design and sketch planning</li>
    <li>Planning and building approvals</li>
    <li>Interior and landscape design</li>
    <li>Project management on site</li>
    <li>Aftercare and maintenance advice</li>
  </ul>
  <h3 class="section-title gallery-title">Our Gallery</h3>
  <div class="gallery">
    <div class="gallery-item a" role="img" aria-label="Photograph of a timber house with wide eaves"></div>
    <div class="gallery-item b" role="img" aria-label="Photograph of a house set among woodland"></div>
    <div class="gallery-item c" role="img" aria-label="Photograph of a warm timber interior"></div>
  </div>
</section>

<footer class="site-footer">
  <div class="footer-col links">
    <h4>Quick Links</h4>
    <p>Home</p><p>About</p><p>Services</p><p>Gallery</p><p>Contact</p>
  </div>
  <div class="footer-col contact">
    <h4>Contact Information</h4>
    <p>12 Harbour Lane, Northgate</p>
    <p>Phone: 0400 218 675</p>
    <p>hello@ashcombestudio.com</p>
  </div>
  <div class="footer-col map">
    <h4>Contact Information</h4>
    <div class="map-box" role="img" aria-label="Street map showing the studio location"></div>
  </div>
  <div class="footer-col follow">
    <h4>Follow Us</h4>
    <div class="social"><span></span>Journal</div>
    <div class="social"><span></span>Updates</div>
    <div class="social"><span></span>Network</div>
  </div>
  <div class="footer-bar">Copyright © 2024 Ashcombe Studio. All Rights Reserved.</div>
</footer>

</body>
</html>
```